Upmarket Dessert Lounge needs a Business Card Design

We are an upmarket dessert lounge needing a business card to match our image.

We want something that is simple yet beautiful, feminine, classy, sophisticated and elegant. We want it to stand out and don't mind if it is bold.

The design should include our logo and colours of red or maroon with gold highlights. We don't mind if black is used.

Marlow & Quince

Target Market(s)

For those who like to indulge or treat themselves and give in to their temptations on good quality desserts.

Industry/Entity Type

Business

Requirements
Must have
• Must include our logo and our name

Marlow & Quince

M & Q

```html
<!DOCTYPE html>
<html lang="en">
<head>
<meta charset="utf-8">
<title>Marlow &amp; Quince — Business Card</title>
<link rel="stylesheet" href="https://fonts.googleapis.com/css2?family=PT+Sans:wght@400;700&display=swap">
<style>
  :root {
    --backdrop: #c9c9c9;
    --card: #ffffff;
    --maroon: #7a1315;
    --peach: #fdd6a0;
    --ink: #3a3a3a;
    --shadow: rgba(0, 0, 0, 0.35);
  }
  * { box-sizing: border-box; margin: 0; padding: 0; }
  html, body {
    width: 956px;
    height: 1200px;
    overflow: hidden;
    background: var(--backdrop);
    font-family: "PT Sans", "Helvetica Neue", Arial, sans-serif;
  }
  .card {
    position: absolute;
    width: 798px;
    height: 458px;
    background: var(--card);
    border-radius: 28px;
    overflow: hidden;
    box-shadow: 6px 8px 14px var(--shadow);
  }
  .card--front { left: 79px; top: 70px; }
  .card--back { left: 73px; top: 632px; height: 456px; }

  .wave { position: absolute; left: 0; top: 0; width: 798px; height: 458px; }

  .brand-name {
    position: absolute;
    transform: translate(-50%, -50%);
    color: var(--maroon);
    font-family: "PT Sans", "Helvetica Neue", Arial, sans-serif;
    font-weight: 400;
    white-space: nowrap;
    line-height: 1;
  }
  .brand-name--monogram {
    left: 217px;
    top: 178px;
    font-size: 78px;
    letter-spacing: 6px;
  }
  .brand-name--full {
    left: 399px;
    top: 228px;
    font-size: 44px;
    letter-spacing: 7px;
  }

  .contact {
    position: absolute;
    left: 427px;
    top: 79px;
    color: var(--ink);
  }
  .contact__name { font-size: 22px; font-weight: 700; line-height: 26px; }
  .contact__role { font-size: 22px; letter-spacing: 1px; line-height: 26px; margin-bottom: 14px; }
  .contact__list { list-style: none; font-size: 19px; line-height: 30px; }
  .contact__list--web { margin-top: 6px; }
  .contact__label { font-weight: 700; }

  .address {
    position: absolute;
    left: 64px;
    top: 373px;
    color: var(--maroon);
    font-size: 19px;
    line-height: 26px;
    font-style: normal;
  }
</style>
</head>
<body>
  <section class="card card--front">
    <svg class="wave" viewBox="0 0 798 458" aria-hidden="true">
      <path fill="var(--peach)" d="M0,318 C250,318 480,440 798,432 L798,458 L0,458 Z"/>
      <path fill="var(--card)" d="M30,321 C300,325 520,420 798,385 L798,436 C520,445 300,345 30,321 Z"/>
      <path fill="var(--maroon)" d="M40,322 C300,330 520,412 798,388 L798,420 C520,430 300,345 40,322 Z"/>
      <path fill="var(--peach)" d="M250,342 C480,390 700,385 798,348 L798,374 C660,398 460,392 250,342 Z"/>
    </svg>

    <div class="brand-name brand-name--monogram">M&amp;Q</div>

    <div class="contact">
      <p class="contact__name">Your Name</p>
      <p class="contact__role">Designation</p>
      <ul class="contact__list">
        <li><span class="contact__label">p</span> : 123-456-7890</li>
        <li><span class="contact__label">c</span> : 123-456-7890</li>
        <li><span class="contact__label">f</span> : 123-456-7890</li>
      </ul>
      <ul class="contact__list contact__list--web">
        <li><span class="contact__label">e</span> : name@yourwebsite.com</li>
        <li><span class="contact__label">w</span> : www.marlowandquince.com</li>
      </ul>
    </div>

    <address class="address">
      0000, Street Name<br>
      City Name, Country Code.
    </address>
  </section>

  <section class="card card--back">
    <div class="brand-name brand-name--full">MARLOW &amp; QUINCE</div>
  </section>
</body>
</html>
```